Tech Savy small Business accountant business card design

We need a business card for a new company based in the cloud. We provide tax, business advisory, accounting, information technology solutions and back office functions to small businesses. We offer fixed fee packages with add on services as you need them. By harnessing technology we simplify small business operational processes providing valuable time and information for small business owners to grow their business. In the logo (bluvoria) we want to be able to see bluv and experts. The final design should communicate achieving growth dreams and balance (ie life and $).
Updates
This project has been temporarily placed on hold until I finalize "Tech Savy small Business accountant needs a logo". I invite all designers to submit on this logo project. Once my logo is finalized I will resume this business card contest. Thanks Added Wednesday, March 19, 2014
This project has been temporarily placed on hold until I finalize "Tech Savy small Business accountant logo". I invite all designers to submit on this logo project. Once my logo is finalized I will resume this business card contest. Thanks Added Thursday, March 20, 2014
Target Market(s)
Small Business (Revenue $500,000, more than 3 employees) owners.
Industry/Entity Type
Small Business
Contact Information for Business Card
Marcy Elwind (Principal)
Accountant, Tax Agent.
TEL | 0417 683 912
EMAIL | Marcy.Elwind@bluvoria.com.au
WEB | www.bluvoria.com.au
Look and feel

```html
<!DOCTYPE html>
<html lang="en">
<head>
<meta charset="utf-8">
<title>bluvoria business card</title>
<link href="https://fonts.googleapis.com/css2?family=Open+Sans:wght@400;600;700&display=swap" rel="stylesheet">
<style>
  :root {
    --page: #e9ebee;
    --card-black: #0b0b0c;
    --brand-blue: #3aa5e0;
    --brand-blue-deep: #1f86c8;
    --rule-grey: #6d6f73;
    --text-white: #ffffff;
    --text-grey: #5f6166;
    --card-white: #ffffff;
  }
  * { margin: 0; padding: 0; box-sizing: border-box; }
  html, body { width: 1200px; height: 913px; overflow: hidden; }
  body {
    background: var(--page);
    font-family: "Open Sans", Arial, sans-serif;
    position: relative;
  }
  .card {
    position: absolute;
    top: 302px;
    width: 540px;
    height: 309px;
    border-radius: 4px;
    overflow: hidden;
    box-shadow: 0 6px 18px rgba(0,0,0,0.18);
  }
  .card-front { left: 40px; background: var(--card-black); }
  .card-back { left: 620px; background: var(--card-white); }

  .name-band {
    position: absolute; left: 0; top: 0; right: 0; height: 104px;
    background: linear-gradient(90deg, var(--brand-blue-deep), var(--brand-blue));
  }
  .band-rule {
    position: absolute; left: 0; right: 0; top: 110px; height: 4px;
    background: var(--rule-grey);
  }

  .holder { position: absolute; left: 26px; top: 30px; color: var(--text-white); }
  .holder-name { font-weight: 700; font-size: 21px; letter-spacing: 0.3px; text-transform: uppercase; line-height: 1.2; }
  .holder-name span { text-transform: none; }
  .holder-title { font-size: 14px; margin-top: 2px; }

  .front-brand { position: absolute; right: 34px; top: 136px; color: var(--text-white); }
  .brand-name { font-weight: 700; font-size: 40px; letter-spacing: -1px; line-height: 1; }
  .brand-tagline { font-size: 11.5px; font-weight: 600; margin-top: 5px; }

  .contacts { position: absolute; left: 26px; bottom: 24px; list-style: none; color: var(--text-white); font-size: 13px; }
  .contacts li { display: flex; align-items: center; gap: 9px; line-height: 20px; }
  .contacts svg { width: 12px; height: 12px; flex: none; }

  .back-brand { position: absolute; left: 0; right: 0; top: 108px; text-align: center; }
  .back-brand .brand-name { color: var(--brand-blue-deep); font-size: 66px; letter-spacing: -2px; }
  .back-brand .brand-tagline { color: var(--text-grey); font-size: 16px; margin-top: 6px; }
</style>
</head>
<body>
  <section class="card card-front" aria-label="Card front">
    <div class="name-band"></div>
    <div class="band-rule"></div>

    <div class="holder">
      <p class="holder-name">Marcy Elwind <span>(Principal)</span></p>
      <p class="holder-title">Accountant, Tax Agent</p>
    </div>

    <div class="front-brand">
      <p class="brand-name">bluvoria</p>
      <p class="brand-tagline">Your business and accounting partner</p>
    </div>

    <ul class="contacts">
      <li>
        <svg viewBox="0 0 12 12"><path d="M2.5 1 L4.5 1 L5 3.5 L3.8 4.4 Q4.8 6.8 7.6 8.2 L8.5 7 L11 7.5 L11 9.5 Q10.5 11 9 11 Q1 10 1 2.5 Q1 1 2.5 1Z" fill="var(--brand-blue)"/></svg>
        0417 683 912
      </li>
      <li>
        <svg viewBox="0 0 12 12"><circle cx="6" cy="6" r="5" fill="none" stroke="var(--brand-blue)" stroke-width="1.2"/><ellipse cx="6" cy="6" rx="2.2" ry="5" fill="none" stroke="var(--brand-blue)" stroke-width="1"/><line x1="1" y1="6" x2="11" y2="6" stroke="var(--brand-blue)" stroke-width="1"/></svg>
        www.bluvoria.com.au
      </li>
      <li>
        <svg viewBox="0 0 12 12"><rect x="1" y="2.5" width="10" height="7" fill="none" stroke="var(--brand-blue)" stroke-width="1.2"/><polyline points="1,2.5 6,6.5 11,2.5" fill="none" stroke="var(--brand-blue)" stroke-width="1.1"/></svg>
        Marcy.Elwind@bluvoria.com.au
      </li>
    </ul>
  </section>

  <section class="card card-back" aria-label="Card back">
    <div class="back-brand">
      <p class="brand-name">bluvoria</p>
      <p class="brand-tagline">Your business and accounting partner</p>
    </div>
  </section>
</body>
</html>
```